Velmarsh Group Webpage Design

We need a new website for our company. The company is Velmarsh Group Pty Ltd. We are in the business of Asbestos Removal; Demolition; Earthworks and Transport. We do not advertise and would like our website to be a reference point for our clients / potential clients and also to make our services known to those searching the internet for the services we offer. Some examples of the style of website we are after are:
http://www.quarnedemolition-example.com.au/
http://m.brintowerdemolitions-example.com.au/
http://www.fenwarddemolition-example.com.au
http://www.tolvik-example.com.au
http://www.ptrservices-example.com.au
http://www.steadfast-dismantling-example.com.au
We will need to work on content. Enclosed is an example. We also need to purchase the domain velmarshgroup-example.com.au and need to set up email accounts and ensure the website is mobile friendly. We have a company logo and have built our business on delivering professional, quality services on time. We would like the webpage to be simple, informative and professional - black and white / grey themed. We would also like to add a photo gallery etc later.

Industry/Entity Type

Construction

Coding

Coded - Design and coding required

Number of Pages Required

1 page

Colors
000000
fcfcfc
959595
dddddd

Requirements
Must have
• Information regarding the services we provide

```html
<!DOCTYPE html>
<html lang="en">
<head>
<meta charset="utf-8">
<title>Velmarsh Group</title>
<link rel="stylesheet" href="https://fonts.googleapis.com/css2?family=Open+Sans:wght@300;400;600&display=swap">
<style>
:root{
  --ink:#000000;
  --dark:#231f20;
  --darker:#1b1819;
  --paper:#fcfcfc;
  --grey:#959595;
  --line:#dddddd;
  --text:#555555;
  --accent:#f7b500;
}
*{margin:0;padding:0;box-sizing:border-box}
html,body{width:794px;height:1200px;overflow:hidden}
body{position:relative;background:#fff;font-family:"Open Sans",Arial,sans-serif;color:var(--text)}
.abs{position:absolute}

.site-header{left:0;top:0;width:794px;height:70px;background:var(--dark)}
.brand{left:66px;top:22px;color:#fff;font-size:19px;font-weight:400;letter-spacing:4.5px;line-height:1}
.brand small{display:block;font-size:7px;letter-spacing:9px;margin-top:6px;padding-left:70px}
.contact-bar{right:64px;top:13px;color:#fff;font-size:10px;display:flex;align-items:center;gap:6px}
.contact-bar svg{width:9px;height:9px}
.contact-bar .sep{margin:0 4px}
.main-nav{right:64px;top:43px;display:flex;gap:25px;font-size:10px;color:#cfcfcf;text-transform:uppercase}
.main-nav .active{color:#fff}
.main-nav .active::before,.main-nav .active::after{content:"";display:inline-block;width:11px;height:1px;background:#fff;vertical-align:middle;margin:0 3px}

.hero{left:0;top:70px;width:794px;height:330px;background:linear-gradient(180deg,#7aa3cc 0%,#b5c3cf 35%,#8d8a86 70%,#5e5650 100%)}
.hero-panel{left:66px;top:102px;width:312px;height:159px;background:rgba(40,38,38,.72)}
.hero-panel h1{position:absolute;left:20px;top:22px;font-size:21px;font-weight:400;color:#fff;line-height:1.2;white-space:nowrap}
.hero-panel p{position:absolute;left:21px;top:53px;width:275px;font-size:8px;color:#d5d5d5;line-height:1.7}
.btn-quote{left:17px;top:97px;width:123px;height:32px;background:var(--accent);color:#fff;font-size:10px;font-weight:600;display:flex;align-items:center;justify-content:center;gap:6px;border-radius:2px}
.dots{left:384px;top:309px;display:flex;gap:6px}
.dots i{width:4px;height:4px;border-radius:50%;background:#999}
.dots i.on{background:#222}

.section-title{left:0;width:794px;text-align:center;font-size:19px;font-weight:400;color:#222;display:flex;justify-content:center;align-items:center;gap:8px}
.section-title::before,.section-title::after{content:"";width:30px;height:1px;background:#222}
.about-text{left:66px;top:453px;width:663px;text-align:center;font-size:8px;line-height:1.7;color:#555}

.service-card{top:590px;width:207px;height:180px;border:1px solid #e6e6e6;text-align:center}
.service-icon{top:546px;width:97px;height:97px;border-radius:50%;background:radial-gradient(circle,#fdfdfd 40%,#e4e4e4 100%)}
.service-card h2{margin-top:68px;font-size:16px;font-weight:400;color:#111}
.service-card p{font-size:8px;line-height:1.7;padding:8px 16px 0;color:#666}
.service-card .more{display:block;margin-top:14px;font-size:7px;color:#222;font-weight:600}

.news-card{top:845px;width:322px;height:131px;background:linear-gradient(180deg,#ffffff,#eeeeee);border:1px solid #e8e8e8}
.news-thumb{left:11px;top:15px;width:94px;height:78px}
.news-body{left:116px;top:16px;width:198px}
.news-body h3{font-size:13px;font-weight:400;color:#111;line-height:1.55}
.news-body .date{font-size:7.5px;color:#888;margin-top:4px}
.news-body p{font-size:7.5px;color:#888;line-height:1.7;margin-top:4px}
.news-body .more{font-size:8px;color:#222;margin-top:6px;display:block}

.site-footer{left:0;top:1010px;width:794px;height:152px;background:var(--dark)}
.foot-col{top:22px;color:#ddd;font-size:8px;line-height:13.6px}
.foot-col h4{font-size:13px;font-weight:400;color:#fff;margin-bottom:8px;line-height:1.2}
.foot-brand{left:542px;top:18px;color:#999;font-size:17px;letter-spacing:4.2px;line-height:1}
.foot-brand small{display:block;font-size:6px;letter-spacing:8px;margin-top:5px;padding-left:66px}
.socials{left:588px;top:63px;display:flex;gap:5.5px}
.socials i{width:19px;height:19px;border-radius:50%;background:#e9e9e9}
.socials i:first-child{background:#6d88c4}
.bottom-bar{left:0;top:1162px;width:794px;height:38px;background:var(--darker);color:#999;font-size:8px;text-align:center;line-height:38px}
</style>
</head>
<body>

<header class="abs site-header">
  <div class="abs brand">VELMARSH<small>GROUP</small></div>
  <div class="abs contact-bar">
    <svg viewBox="0 0 10 10"><path d="M2 1l2 2-1 1.5c.6 1.2 1.3 1.9 2.5 2.5L7 6l2 2-1.3 1.5C4.5 9 1 5.5.5 2.3z" fill="#f7b500"/></svg>
    <span>0400 318 562</span><span class="sep">|</span>
    <svg viewBox="0 0 10 10"><rect x=".5" y="2" width="9" height="6" fill="#f7b500"/><path d="M.5 2l4.5 3.5L9.5 2" stroke="#231f20" fill="none"/></svg>
    <span>vtdemolition@example-mail.com</span>
  </div>
  <nav class="abs main-nav">
    <span class="active">Home</span><span>About Us</span><span>Services</span><span>Safety</span><span>Environment</span><span>Contact Us</span>
  </nav>
</header>

<section class="abs hero" role="img" aria-label="Excavator demolishing a commercial building under a blue sky">
  <div class="abs hero-panel">
    <h1>COMMERCIAL DEMOLITION</h1>
    <p>A large amount of experience across a broad range of projects results in a dependable service and peace of mind for all clients.</p>
    <div class="abs btn-quote">
      <svg width="10" height="10" viewBox="0 0 10 10"><rect x="1" y="2" width="7" height="7" fill="none" stroke="#fff"/><path d="M4 6l5-5" stroke="#fff" stroke-width="1.4"/></svg>
      REQUEST QUOTE
    </div>
  </div>
  <div class="abs dots"><i></i><i class="on"></i><i></i></div>
</section>

<h2 class="abs section-title" style="top:419px">ABOUT US</h2>
<p class="abs about-text">Velmarsh Transport Pty Ltd was established by Director Marcus Velmarsh in 2002 with a focus providing services within the transport industry. Over time the company has developed and expanded to include the provision of Earthworks and Demolition. Marcus has over 10 years' experience working at all levels within these industries focusing primarily on Demolition and Earthworks in recent times.</p>

<h2 class="abs section-title" style="top:509px">SERVICES</h2>

<article class="abs service-card" style="left:66px"><h2>DEMOLITION</h2><p>Velmarsh Transport and Demolition provide an extensive range of demolition services. A large amount of experience</p><span class="more">READ MORE</span></article>
<article class="abs service-card" style="left:293px"><h2>EARTHWORKS</h2><p>Velmarsh Transport and Demolition provide an extensive range of demolition services. A large amount of experience</p><span class="more">READ MORE</span></article>
<article class="abs service-card" style="left:521px"><h2>ASBESTOS</h2><p>Velmarsh Transport and Demolition provide an extensive range of demolition services. A large amount of experience</p><span class="more">READ MORE</span></article>
<div class="abs service-icon" style="left:121px" role="img" aria-label="Crane with wrecking ball icon"></div>
<div class="abs service-icon" style="left:348px" role="img" aria-label="Bulldozer icon"></div>
<div class="abs service-icon" style="left:577px" role="img" aria-label="Asbestos removal worker icon"></div>

<h2 class="abs section-title" style="top:797px">RECENT NEWS</h2>

<article class="abs news-card" style="left:66px">
  <div class="abs news-thumb" role="img" aria-label="Excavator at a house demolition site" style="background:linear-gradient(160deg,#c9c3b8,#8a6f55 60%,#6e655b)"></div>
  <div class="abs news-body"><h3>WE HAVE RECENTLY ADDED A NUMBER OF DEMOLITION</h3><div class="date">Nov27,2015</div><p>Neque porro quisquam est, qui dolorem ipsum quia dolor sit amet, consectetur voluptateam.</p><span class="more">Read More</span></div>
</article>
<article class="abs news-card" style="left:406px">
  <div class="abs news-thumb" role="img" aria-label="Yellow excavator against a cloudy blue sky" style="background:linear-gradient(170deg,#3f7fcf,#9cc1e6 55%,#d99a3a)"></div>
  <div class="abs news-body"><h3>WE HAVE RECENTLY ADDED A NUMBER OF DEMOLITION</h3><div class="date">Nov27,2015</div><p>Neque porro quisquam est, qui dolorem ipsum quia dolor sit amet, consectetur voluptateam.</p><span class="more">Read More</span></div>
</article>

<footer class="abs site-footer">
  <div class="abs foot-col" style="left:66px"><h4>QUICK LINKS</h4>Home<br>About Us<br>Services<br>Safety<br>Environment<br>Contact Us</div>
  <div class="abs foot-col" style="left:219px"><h4>SERVICES</h4>Demolition<br>Earthworks<br>Asbestos</div>
  <div class="abs foot-col" style="left:343px"><h4>CONTACT US</h4>PO Box 512 HARLOWVALE QLD 4190<br><br>0400 318 562<br>vtdemolition@example-mail.com</div>
  <div class="abs foot-brand">VELMARSH<small>GROUP</small></div>
  <div class="abs socials"><i></i><i></i><i></i><i></i><i></i><i></i></div>
</footer>
<div class="abs bottom-bar">© 2015 Velmarsh Group Pty Ltd. All rights reserved.</div>

</body>
</html>
```